physical therapy flyer

2 office locations speciality programs - work injury / Motor vehicle accidents - spanish speaking - do not put balance defecits/ fall prevention - Spanish speaking
neck and back pain shoulder pain/ rotator cuff disorder / bursitis
hip pain knee andle and foot pain post operative care including Spine , shoulder , knee , total joint replacement

Meadowlark Physical therapy & Chiropractic
4871 Pinecrest BLvd
dalton heights ny 10592
7185820147
3715 Tillman Parkway
Fernvale NY 10592
7189043218
www.meadowlarkptrehab.com

```html
<!DOCTYPE html>
<html lang="en">
<head>
<meta charset="UTF-8">
<title>Meadowlark Physical Therapy Flyer</title>
<link rel="stylesheet" href="https://fonts.googleapis.com/css2?family=Allura&family=Montserrat:wght@300;400;600;700;800&family=Playfair+Display:wght@600;700&display=swap">
<style>
  :root {
    --green-dark: #0f8a3c;
    --green-mid: #43a33e;
    --green-light: #86c14b;
    --green-bright: #7cc242;
    --ink: #222222;
    --charcoal: #333333;
    --white: #ffffff;
    --paper: #ffffff;
  }
  * { box-sizing: border-box; margin: 0; padding: 0; }
  html, body { width: 900px; height: 1200px; overflow: hidden; background: var(--paper); }
  .flyer { position: relative; width: 900px; height: 1200px; background: var(--paper); font-family: 'Montserrat', sans-serif; color: var(--ink); overflow: hidden; }

  .brand { position: absolute; left: 40px; top: 40px; display: flex; align-items: center; gap: 10px; }
  .brand-dot { width: 34px; height: 34px; border-radius: 50%; background: var(--green-dark); flex: none; }
  .brand-name { font-family: 'Montserrat', sans-serif; font-weight: 400; font-size: 16px; line-height: 20px; color: var(--green-dark); }

  .headline-top { position: absolute; left: 38px; top: 140px; font-family: 'Playfair Display', serif; font-weight: 700; font-size: 80px; line-height: 1; color: var(--green-bright); letter-spacing: -2px; }
  .headline-script { position: absolute; left: 52px; top: 195px; font-family: 'Allura', cursive; font-size: 130px; line-height: 1; color: var(--green-dark); z-index: 2; }
  .headline-box { position: absolute; left: 40px; top: 297px; width: 354px; height: 91px; background: var(--green-mid); border-radius: 6px; }
  .headline-box span { position: absolute; left: 14px; top: 2px; font-family: 'Playfair Display', serif; font-weight: 700; font-size: 76px; line-height: 1.1; color: var(--white); letter-spacing: -1px; }

  .intro { position: absolute; left: 40px; top: 412px; width: 400px; font-size: 14.6px; font-weight: 400; line-height: 20px; color: var(--ink); }

  .photo-top { position: absolute; left: 535px; top: 0; width: 365px; height: 300px; background: linear-gradient(160deg, #e4d3bd 0%, #b7a58f 45%, #8f9a9c 100%); }

  .programs { position: absolute; left: 470px; top: 299px; width: 430px; height: 364px; background: var(--green-light); border-radius: 8px 0 0 8px; color: var(--white); }
  .programs h2 { position: absolute; left: 27px; top: 22px; font-family: 'Playfair Display', serif; font-weight: 600; font-size: 34px; line-height: 38px; }
  .spine-art { position: absolute; left: 744px; top: 190px; width: 156px; height: 343px; border-radius: 60px 0 0 60px; background: linear-gradient(180deg, #c9d9e6 0%, #8fb0cc 45%, #f0793a 55%, #d8c9a5 100%); opacity: .85; }
  .program-list { position: absolute; left: 27px; top: 112px; list-style: none; width: 340px; }
  .program-list li { position: relative; padding-left: 25px; font-size: 15px; line-height: 17px; margin-bottom: 8.6px; }
  .program-list li::before { content: ""; position: absolute; left: 0; top: 4px; border-left: 7px solid var(--green-dark); border-top: 5px solid transparent; border-bottom: 5px solid transparent; }
  .program-list li.wide { width: 300px; }

  .photo-bottom { position: absolute; left: 0; top: 700px; width: 470px; height: 500px; background: linear-gradient(120deg, #3e5868 0%, #a8b3b5 50%, #c9c7bd 100%); border-top-right-radius: 6px; }

  .cta { position: absolute; left: 440px; top: 705px; width: 260px; height: 210px; }
  .cta-top { font-family: 'Montserrat', sans-serif; font-weight: 700; font-size: 22px; fill: var(--white); }
  .cta-main { font-family: 'Montserrat', sans-serif; font-weight: 800; font-size: 40px; fill: var(--white); }

  .contacts { position: absolute; left: 536px; top: 925px; width: 340px; }
  .contact-row { display: flex; align-items: flex-start; gap: 12px; font-weight: 600; font-size: 19px; line-height: 25px; color: var(--ink); margin-bottom: 8px; }
  .contact-row svg { flex: none; width: 20px; height: 22px; margin-top: 2px; }
  .divider { height: 1px; background: var(--green-dark); width: 280px; margin: 6px 0 12px; }
</style>
</head>
<body>
<main class="flyer">
  <div class="photo-top" role="img" aria-label="Photo of a smiling older man exercising with dumbbells while a therapist rests her hands on his shoulders"></div>

  <header class="brand">
    <span class="brand-dot"></span>
    <p class="brand-name">Meadowlark Physical Therapy,<br>Chiropractic, and Acupuncture</p>
  </header>

  <h1>
    <span class="headline-top">We Create</span>
    <span class="headline-script">Healthy</span>
    <span class="headline-box"><span>Families</span></span>
  </h1>

  <p class="intro">Meadowlark Physical Therapy, Chiropractic &amp; Acupuncture offers relief for many discomforts, including neck pain, back pain, arm pain and knee pain. These musculoskeletal disorders are examined by one of our three chiropractors who take a personal approach to your chiropractic care. Whether you are suffering from sports related injuries, orthopedic complaints, have been in an automobile accident or have been injured at work, our chiropractor welcomes the opportunity to care for you.</p>

  <section class="programs">
    <h2>Speciality<br>Programs</h2>
    <ul class="program-list">
      <li>Work injury.</li>
      <li>Motor vehicle accidents.</li>
      <li>Spanish speaking.</li>
      <li>Neck, back &amp; shoulder pain.</li>
      <li>Rotator cuff disorder.</li>
      <li class="wide">Bursitis hip pain knee handle<br>&amp; foot pain.</li>
      <li style="width:400px">Post Operative Care including Spine,<br>shoulder, knee , total joint replacement.</li>
    </ul>
  </section>
  <div class="spine-art" role="img" aria-label="Illustration of a human spine with a highlighted area of pain in the lower back"></div>

  <div class="photo-bottom" role="img" aria-label="Photo of a physical therapist with a clipboard talking with an older male patient seated on a treatment bed"></div>

  <svg class="cta" viewBox="0 0 260 210" aria-label="Book your session">
    <polygon points="4,62 252,7 256,120 118,135 86,202 72,160 18,165" fill="var(--charcoal)"/>
    <rect x="18" y="21" width="207" height="39" rx="8" fill="var(--green-light)"/>
    <text class="cta-top" x="40" y="50">BOOK YOUR</text>
    <text class="cta-main" x="22" y="131">SESSION</text>
  </svg>

  <section class="contacts">
    <div class="contact-row">
      <svg viewBox="0 0 24 24"><path fill="var(--green-bright)" d="M6.6 10.8a15.1 15.1 0 0 0 6.6 6.6l2.2-2.2c.3-.3.7-.4 1-.2 1.1.4 2.3.6 3.6.6.6 0 1 .4 1 1V20c0 .6-.4 1-1 1A17 17 0 0 1 3 4c0-.6.4-1 1-1h3.5c.6 0 1 .4 1 1 0 1.3.2 2.5.6 3.6.1.3 0 .7-.2 1z"/></svg>
      <span>7185820147</span>
    </div>
    <div class="contact-row">
      <svg viewBox="0 0 24 24"><path fill="var(--green-dark)" d="M12 2a7 7 0 0 0-7 7c0 5.2 7 13 7 13s7-7.8 7-13a7 7 0 0 0-7-7zm0 9.5A2.5 2.5 0 1 1 12 6.5a2.5 2.5 0 0 1 0 5z"/></svg>
      <span>4871 Pinecrest BLvd<br>dalton heights ny 10592</span>
    </div>
    <div class="divider"></div>
    <div class="contact-row">
      <svg viewBox="0 0 24 24"><path fill="var(--green-bright)" d="M6.6 10.8a15.1 15.1 0 0 0 6.6 6.6l2.2-2.2c.3-.3.7-.4 1-.2 1.1.4 2.3.6 3.6.6.6 0 1 .4 1 1V20c0 .6-.4 1-1 1A17 17 0 0 1 3 4c0-.6.4-1 1-1h3.5c.6 0 1 .4 1 1 0 1.3.2 2.5.6 3.6.1.3 0 .7-.2 1z"/></svg>
      <span>7189043218</span>
    </div>
    <div class="contact-row">
      <svg viewBox="0 0 24 24"><path fill="var(--green-dark)" d="M12 2a7 7 0 0 0-7 7c0 5.2 7 13 7 13s7-7.8 7-13a7 7 0 0 0-7-7zm0 9.5A2.5 2.5 0 1 1 12 6.5a2.5 2.5 0 0 1 0 5z"/></svg>
      <span>3715 Tillman Parkway<br>Fernvale NY 10592</span>
    </div>
    <div class="contact-row">
      <svg viewBox="0 0 24 24"><path fill="var(--green-bright)" d="M5 3l14 9-6 1.5 3.5 6.5-2.5 1.3-3.5-6.6L6 19z"/></svg>
      <span>meadowlarkptrehab.com</span>
    </div>
  </section>
</main>
</body>
</html>
```